Business card for a new innovative and professional lawn care business

We need a business card design for a new lawn care business in Halifax NS Canada. We offer lawn services in Halifax & Bedford. Our services offered include lawn care, garden services, and property maintenance. We take pride in our work and are experienced at what we do. I would like to see a design that is double sided. On the backside I would like the something simple (maybe my logo preferably on blackround (linked below) with website link, Facebook page or something). The front I want to include contact info:
Morgan Pell
phone 902-555-0148
email - brookvaleyards.ca
facebook - Facebook.com/brookvaleyards
Instagram maybe ? - instagram.com/brookvaleyard
Serving Halifax and Bedford for 5 years?
I don't want it to have too much information as I will be passing them out in aim to visit website, or call !
We do want it to include lawn care, garden services and property maintenance.
Basic, catchy, and modern looking !
Logo attached below !

Target Market(s)

Passing business cards to everyone I meet or interact with.

Industry/Entity Type

Lawn Care

Contact Information for Business Card

Double sided with some basic information, with catchy colours and easy to look at.

Font styles to use
Sans Serif

Requirements
Must have
• Must be double sided and have :
• Name, Phone, Email, FB, Website, and 3 main services offered - lawn care, property maintenance, garden services
Nice to have
• Would be nice to have instagram link if it goes well on there
Should not have
• Don't want too much writing or images that are distracting

```html
<!DOCTYPE html>
<html lang="en">
<head>
<meta charset="utf-8">
<title>Brookvale Yards – Business Card</title>
<link rel="stylesheet" href="https://fonts.googleapis.com/css2?family=Open+Sans:wght@400;600;700&family=PT+Sans+Narrow&display=swap">
<style>
  :root {
    --page: #e9e6df;
    --card-white: #ffffff;
    --leaf: #8cc63f;
    --leaf-dark: #1f7a3a;
    --ink: #555b55;
    --on-green: #ffffff;
  }
  * { margin: 0; padding: 0; box-sizing: border-box; }
  html, body { width: 1200px; height: 950px; overflow: hidden; }
  body {
    background: var(--page);
    font-family: "Open Sans", sans-serif;
    position: relative;
  }
  .card {
    position: absolute;
    left: 250px;
    width: 700px;
    height: 400px;
    box-shadow: 0 6px 18px rgba(0,0,0,.18);
    overflow: hidden;
  }
  .card--front { top: 60px; background: var(--card-white); }
  .card--back { top: 490px; background: var(--leaf); }

  /* front */
  .corner-tab {
    position: absolute; top: 0; right: 40px;
    width: 34px; height: 18px; background: var(--leaf-dark);
  }
  .person {
    position: absolute; top: 44px; right: 40px; text-align: right;
  }
  .person__name {
    color: var(--leaf); font-weight: 600; font-size: 26px; line-height: 1.2;
  }
  .person__email {
    font-family: "PT Sans Narrow", sans-serif;
    color: var(--ink); font-size: 21px; margin-top: 4px;
  }
  .brand {
    position: absolute;
    font-weight: 700; font-size: 40px; letter-spacing: 1px;
    white-space: nowrap;
    display: flex; align-items: center; gap: 14px;
  }
  .brand__dot {
    width: 34px; height: 34px; border-radius: 50%; background: currentColor; flex: none;
  }
  .brand--front { left: 70px; top: 158px; color: var(--leaf-dark); }
  .contacts {
    position: absolute; left: 74px; bottom: 36px; list-style: none;
    font-family: "PT Sans Narrow", sans-serif; font-size: 20px; color: var(--ink);
  }
  .contacts li { display: flex; align-items: center; gap: 10px; height: 28px; }
  .contacts svg { width: 16px; height: 16px; flex: none; }

  /* back */
  .brand--back {
    left: 0; right: 0; top: 140px; justify-content: center; color: var(--on-green);
  }
  .services {
    position: absolute; left: 0; right: 0; bottom: 48px;
    display: flex; justify-content: center; gap: 28px;
    font-family: "PT Sans Narrow", sans-serif; font-size: 22px; color: var(--on-green);
  }
  .services span { display: flex; align-items: center; gap: 8px; }
  .services svg { width: 16px; height: 16px; }
</style>
</head>
<body>

<section class="card card--front" aria-label="Card front">
  <div class="corner-tab"></div>
  <div class="person">
    <p class="person__name">Morgan Pell</p>
    <p class="person__email">info@brookvaleyards.ca</p>
  </div>

  <p class="brand brand--front"><span class="brand__dot"></span>Brookvale Yards</p>

  <ul class="contacts">
    <li>
      <svg viewBox="0 0 16 16"><path d="M4 1.5 6.5 4 5 6c.8 1.9 2.3 3.4 4.2 4.2l2-1.5L13.7 11 12 13.8C6.6 13.4 2.6 9.4 2.2 4z" fill="#8cc63f"/></svg>
      902-555-0148
    </li>
    <li><svg viewBox="0 0 16 16"><circle cx="8" cy="8" r="7" fill="#8cc63f"/></svg>brookvaleyards.ca</li>
    <li><svg viewBox="0 0 16 16"><circle cx="8" cy="8" r="7" fill="#8cc63f"/></svg>brookvaleyards</li>
    <li><svg viewBox="0 0 16 16"><circle cx="8" cy="8" r="7" fill="#8cc63f"/></svg>brookvaleyard</li>
  </ul>
</section>

<section class="card card--back" aria-label="Card back">
  <p class="brand brand--back"><span class="brand__dot"></span>Brookvale Yards</p>
  <div class="services">
    <span><svg viewBox="0 0 16 16"><path d="M2 14C2 6 7 2 14 2c0 7-4 12-12 12z" fill="#fff"/></svg>Lawn Care</span>
    <span><svg viewBox="0 0 16 16"><path d="M2 14C2 6 7 2 14 2c0 7-4 12-12 12z" fill="#fff"/></svg>Property Maintenance</span>
    <span><svg viewBox="0 0 16 16"><path d="M2 14C2 6 7 2 14 2c0 7-4 12-12 12z" fill="#fff"/></svg>Garden Services</span>
  </div>
</section>

</body>
</html>
```